Copper Kettle Fitness Flyer

We need a Flyer designed for a Revolutionary Fresh New Functional Fitness facility in Manly Sydney, Australia. We have just recently opened and now need to get the word out. Using the flyers to hand out at events also for shop counters and letterbox drops.

Our company name is Copper Kettle Fitness "Where STRENGTH Is Your FORTUNE".
We promote health and fitness to all fitness levels concentrating on functional fitness. To learn more about us and our colour scheme see attached file and also check us out on www.brightwavesocial.example/copperkettlefitnessaus

A5 Size please

Target Market(s)

The beauty of our system is it is for everyone we have girls and guys in there teens, 20's 30's 40's and 50's. Not only that we have professional athletes, military and high fitness levels all the way to people who are overweight and need to loose weight and tone up. The system caters for everyone.

Industry/Entity Type

Fitness

Requirements
Must have
• FRONT:

Free 30min Fat Blasting Experience With Your Very Own Personal Trainer !!!

New Class Starts Every 3 minutes.
30 minute Workout With A Trainer.
No Machines No Mirrors And No Attitudes.
Catering For All Fitness Levels.
Results Guaranteed Or Your Money Back.
Fun, Fresh, Clean, Revolutionary New Facility.

Back:

You Are Just Moments Away From Burning Fat Faster Than Ever Before And Getting That Body You Always Wanted !!!

Come In Today To Claim Your FREE Workout.

Ph (02) 9418 7260
Address 5/217 Harlow St North Manly 2100
www.brightwavesocial.example/copperkettlefitnessaus
Nice to have
• FRONT:

Back:

Ph (02) 9418 7260

```html
<!DOCTYPE html>
<html lang="en">
<head>
<meta charset="utf-8">
<title>Copper Kettle Fitness Flyer</title>
<link rel="stylesheet" href="https://fonts.googleapis.com/css2?family=Oswald:wght@500;700&family=Roboto+Condensed:ital,wght@0,400;0,700;1,700&display=swap">
<style>
:root{
  --pink:#ec1c8c;
  --blue:#1b75bc;
  --blue-light:#2aa9e0;
  --blue-dark:#0d5ea8;
  --orange:#f7941d;
  --orange-deep:#f26522;
  --yellow:#ffe600;
  --white:#ffffff;
  --ink:#3a3a3a;
  --grey:#6f6f6f;
}
*{margin:0;padding:0;box-sizing:border-box}
html,body{width:865px;height:1200px;overflow:hidden;background:var(--white)}
.flyer{position:relative;width:865px;height:1200px;overflow:hidden;background:var(--white);font-family:"Roboto Condensed",Arial,sans-serif}
.photo{position:absolute}
.photo--dumbbell{left:0;top:0;width:410px;height:470px;background:linear-gradient(160deg,#e9e3de 0%,#d6b9a3 45%,#8c8c8c 100%)}
.photo--waist{left:540px;top:380px;width:300px;height:400px;background:linear-gradient(180deg,#e7c6ab 0%,#f3ede8 50%,#d9c3b0 100%);border-radius:0 0 40px 40px}
.photo--stretch{left:0;top:850px;width:480px;height:350px;background:linear-gradient(200deg,#eadbd0 0%,#d1a98b 50%,#9aa7b3 100%)}
.waves{position:absolute;inset:0}
.headline{position:absolute;left:432px;top:60px;width:420px;font-family:"Oswald",Impact,sans-serif;font-weight:700;text-transform:uppercase}
.headline__main{display:block;color:var(--pink);font-size:58px;line-height:1.06}
.headline__sub{display:block;color:var(--blue);font-size:37px;line-height:1.12;margin-top:14px}
.badge{position:absolute;left:36px;top:290px;width:180px;height:180px;border-radius:50%;background:var(--orange);border:5px solid var(--white);box-shadow:0 3px 8px rgba(0,0,0,.25);display:flex;flex-direction:column;align-items:center;justify-content:center;text-align:center;color:var(--white);text-transform:uppercase;transform:rotate(-12deg)}
.badge__strong{font-family:"Oswald",Impact,sans-serif;font-weight:700;font-size:24px;line-height:1.05}
.badge__small{font-weight:700;font-size:15px;line-height:1.15;margin-top:4px}
.benefits{position:absolute;left:50px;top:545px;list-style:none}
.benefits li{display:flex;align-items:center;gap:12px;color:var(--white);font-style:italic;font-weight:700;font-size:24px;line-height:1;margin-bottom:16px;text-shadow:0 1px 2px rgba(0,0,0,.25)}
.tick{flex:none;width:24px;height:24px}
.moments{position:absolute;left:50px;top:752px;width:470px;color:var(--yellow);font-weight:700;font-size:16px;line-height:1.25}
.claim{position:absolute;left:520px;top:835px;width:330px;color:var(--white);text-transform:uppercase}
.claim__lead{font-family:"Oswald",Impact,sans-serif;font-weight:500;font-size:21px}
.claim__offer{font-family:"Oswald",Impact,sans-serif;font-weight:700;font-size:40px;line-height:1.1}
.claim__phone{display:flex;align-items:center;gap:10px;font-family:"Oswald",Impact,sans-serif;font-weight:700;font-size:44px;margin-top:6px}
.claim__phone svg{width:34px;height:34px}
.brand{position:absolute;left:540px;top:1030px;display:flex;align-items:center;gap:16px}
.brand__mark{width:72px;height:72px;background:var(--orange-deep)}
.brand__name{font-family:"Oswald",Impact,sans-serif;font-weight:500;font-size:30px;line-height:1.02;color:var(--ink);text-transform:uppercase}
.contact{position:absolute;left:520px;top:1114px;width:330px;font-size:13px;line-height:1.4;color:var(--grey)}
.contact__tagline{font-weight:700;color:var(--ink)}
</style>
</head>
<body>
<main class="flyer">
  <div class="photo photo--dumbbell" role="img" aria-label="Smiling woman lifting a dumbbell"></div>

  <svg class="waves" viewBox="0 0 865 1200" aria-hidden="true">
    <defs>
      <linearGradient id="blueBand" x1="0" y1="0" x2="1" y2="1">
        <stop offset="0" stop-color="#2aa9e0"/>
        <stop offset="1" stop-color="#0d5ea8"/>
      </linearGradient>
      <linearGradient id="orangeBand" x1="0" y1="0" x2="1" y2="0">
        <stop offset="0" stop-color="#f26522"/>
        <stop offset="1" stop-color="#f7941d"/>
      </linearGradient>
    </defs>
    <path d="M0,440 C260,400 560,490 865,360 L865,470 C560,560 260,480 0,520 Z" fill="#ffffff"/>
    <path d="M0,500 C260,460 560,540 865,420 L865,800 C600,760 300,860 0,820 Z" fill="url(#blueBand)"/>
    <path d="M0,820 C300,870 600,780 865,790 L865,1005 C650,1030 480,990 0,1040 Z" fill="url(#orangeBand)"/>
  </svg>

  <div class="photo photo--waist" role="img" aria-label="Slim woman in oversized jeans showing weight loss"></div>
  <div class="photo photo--stretch" role="img" aria-label="Woman in sportswear stretching on the floor"></div>

  <h1 class="headline">
    <span class="headline__main">Free 30min<br>Fat Blasting<br>Experience</span>
    <span class="headline__sub">With your very own<br>personal trainer !!!</span>
  </h1>

  <div class="badge">
    <span class="badge__strong">Results<br>Guaranteed</span>
    <span class="badge__small">Or your money<br>back.</span>
  </div>

  <ul class="benefits">
    <li><svg class="tick" viewBox="0 0 24 24"><circle cx="12" cy="12" r="12" fill="#ffe600"/><path d="M6.5 12.5l3.5 3.5 7-8" fill="none" stroke="#0d5ea8" stroke-width="2.6"/></svg>New Class Starts Every 3 minutes.</li>
    <li><svg class="tick" viewBox="0 0 24 24"><circle cx="12" cy="12" r="12" fill="#ffe600"/><path d="M6.5 12.5l3.5 3.5 7-8" fill="none" stroke="#0d5ea8" stroke-width="2.6"/></svg>30 minute Workout With A Trainer.</li>
    <li><svg class="tick" viewBox="0 0 24 24"><circle cx="12" cy="12" r="12" fill="#ffe600"/><path d="M6.5 12.5l3.5 3.5 7-8" fill="none" stroke="#0d5ea8" stroke-width="2.6"/></svg>No Machines No Mirrors And No Attitudes.</li>
    <li><svg class="tick" viewBox="0 0 24 24"><circle cx="12" cy="12" r="12" fill="#ffe600"/><path d="M6.5 12.5l3.5 3.5 7-8" fill="none" stroke="#0d5ea8" stroke-width="2.6"/></svg>Fun, Fresh, Clean, Revolutionary New Facility.</li>
    <li><svg class="tick" viewBox="0 0 24 24"><circle cx="12" cy="12" r="12" fill="#ffe600"/><path d="M6.5 12.5l3.5 3.5 7-8" fill="none" stroke="#0d5ea8" stroke-width="2.6"/></svg>Catering For All Fitness Levels.</li>
  </ul>

  <p class="moments">You Are Just Moments Away From Burning Fat Faster Than Ever Before And Getting That Body You Always Wanted !!!</p>

  <div class="claim">
    <p class="claim__lead">Come in today to claim your</p>
    <p class="claim__offer">Free Workout.</p>
    <p class="claim__phone"><svg viewBox="0 0 24 24"><circle cx="12" cy="12" r="11" fill="none" stroke="#fff" stroke-width="2"/><path d="M8.2 6.5l2 2.2-1 1.5c.7 1.6 2 2.9 3.6 3.6l1.5-1 2.2 2-1.2 1.8c-3.8-.4-7.5-4.1-7.9-7.9z" fill="#fff"/></svg>(02) 9418 7260</p>
  </div>

  <div class="brand">
    <span class="brand__mark"></span>
    <span class="brand__name">Copper Kettle<br>Fitness</span>
  </div>
  <div class="contact">
    <p class="contact__tagline">Where STRENGTH Is Your FORTUNE</p>
    <p>5/217 Harlow St North Manly 2100</p>
    <p>www.brightwavesocial.example/copperkettlefitnessaus</p>
  </div>
</main>
</body>
</html>
```